Hartwell Estates Business Cards

I would like a business card that includes myself and my partner.
Includes: Logo, office #, email, website, our names, our numbers and possibly the address. I would also like the logo to be embossed and the card to be horizontal.
There is a photo of our yard signs to give you an idea of the colors of our business.

Target Market(s)

Everyone in real estate market.
We are in a rural area. Our clientele are from all socioeconomic backgrounds.

Industry/Entity Type

Real Estate Agent

Contact Information for Business Card

Company Name: Hartwell Estates
Our Names, Titles & Cell #'s : Dana Pembrook-Broker (555).317.6624, Marla Pembrook-Realtor (555).609.1385
Office #: (555).240.3918
Website: hartwellestates-demo.com
Joint Email: pembrook@hartwellestates-demo.com
Office Address: 418B W. Calloway Ave.
Larkmoor, KS. 70913

Font styles to use
Serif

Requirements
Must have
• HORIZONTAL, Logo, Myself and my partners names, Our cell #'s, our office #, our website, our email address
Nice to have
• Embossed logo, office address, our titles.

```html
<!DOCTYPE html>
<html lang="en">
<head>
<meta charset="utf-8">
<title>Hartwell Estates Business Cards</title>
<link href="https://fonts.googleapis.com/css2?family=Noto+Serif:wght@400;700&family=Open+Sans:wght@400&display=swap" rel="stylesheet">
<style>
  :root {
    --purple: #4a2470;
    --purple-soft: #6b4190;
    --ink: #1c1c1c;
    --card: #f7f7f7;
    --backdrop: #e6e4e1;
  }
  * { box-sizing: border-box; margin: 0; padding: 0; }
  html, body { width: 1200px; height: 443px; overflow: hidden; }
  body {
    background: var(--backdrop);
    position: relative;
    font-family: "Open Sans", Arial, sans-serif;
  }
  .card {
    position: absolute;
    top: 86px;
    width: 478px;
    height: 272px;
    background: var(--card);
    border-radius: 16px;
  }
  .card--front { left: 98px; }
  .card--back { left: 624px; }

  .brand {
    position: absolute;
    left: 26px;
    top: 40px;
    display: flex;
    align-items: center;
    gap: 8px;
  }
  .brand__dot {
    width: 14px; height: 14px;
    border-radius: 50%;
    background: var(--purple);
  }
  .brand__name {
    font-family: "Noto Serif", Georgia, serif;
    font-weight: 700;
    font-size: 19px;
    color: var(--purple);
  }

  .agent {
    position: absolute;
    left: 298px;
    padding-left: 10px;
    border-left: 4px solid var(--purple);
    height: 66px;
  }
  .agent--realtor { top: 26px; }
  .agent--broker { top: 179px; }
  .agent__name {
    font-family: "Noto Serif", Georgia, serif;
    font-size: 19px;
    line-height: 24px;
    color: var(--ink);
  }
  .agent__title {
    font-family: "Noto Serif", Georgia, serif;
    font-size: 13px;
    line-height: 16px;
    color: var(--purple-soft);
  }
  .agent__phone {
    display: flex;
    align-items: center;
    gap: 6px;
    margin-top: 4px;
    font-size: 12px;
    color: var(--ink);
  }

  .contact {
    position: absolute;
    left: 30px;
    top: 130px;
    list-style: none;
  }
  .contact__item {
    display: flex;
    align-items: flex-start;
    gap: 10px;
    font-size: 11.5px;
    line-height: 16px;
    color: var(--ink);
    margin-bottom: 4px;
  }
  .contact__item--gap { margin-top: 12px; }
  .icon { width: 14px; height: 14px; flex: none; fill: var(--purple); margin-top: 1px; }
  .icon--tall { width: 10px; height: 14px; margin-top: 0; }

  .emboss {
    position: absolute;
    inset: 0;
    display: flex;
    align-items: center;
    justify-content: center;
    gap: 12px;
  }
  .emboss__dot {
    width: 36px; height: 36px;
    border-radius: 50%;
    background: var(--purple);
  }
  .emboss__name {
    font-family: "Noto Serif", Georgia, serif;
    font-weight: 700;
    font-size: 34px;
    color: var(--purple);
  }
</style>
</head>
<body>

<section class="card card--front">
  <div class="brand">
    <span class="brand__dot"></span>
    <span class="brand__name">Hartwell Estates</span>
  </div>

  <div class="agent agent--realtor">
    <p class="agent__name">Marla Pembrook</p>
    <p class="agent__title">Realtor</p>
    <p class="agent__phone">
      <svg class="icon icon--tall" viewBox="0 0 10 14"><path d="M1.5 0h7A1.5 1.5 0 0 1 10 1.5v11A1.5 1.5 0 0 1 8.5 14h-7A1.5 1.5 0 0 1 0 12.5v-11A1.5 1.5 0 0 1 1.5 0zM1.5 1.5v9.5h7V1.5zM5 11.8a.9.9 0 1 0 0 1.8.9.9 0 0 0 0-1.8z"/></svg>
      (555).609.1385
    </p>
  </div>

  <div class="agent agent--broker">
    <p class="agent__name">Dana Pembrook</p>
    <p class="agent__title">Broker</p>
    <p class="agent__phone">
      <svg class="icon icon--tall" viewBox="0 0 10 14"><path d="M1.5 0h7A1.5 1.5 0 0 1 10 1.5v11A1.5 1.5 0 0 1 8.5 14h-7A1.5 1.5 0 0 1 0 12.5v-11A1.5 1.5 0 0 1 1.5 0zM1.5 1.5v9.5h7V1.5zM5 11.8a.9.9 0 1 0 0 1.8.9.9 0 0 0 0-1.8z"/></svg>
      (555).317.6624
    </p>
  </div>

  <ul class="contact">
    <li class="contact__item">
      <svg class="icon" viewBox="0 0 14 14"><path d="M1 4c0-1.5 2.5-2.5 6-2.5S13 2.5 13 4v1.2h-3V4H4v1.2H1zM3.5 6h7l2 5.5H1.5zM7 7.6a1.4 1.4 0 1 0 0 2.8 1.4 1.4 0 0 0 0-2.8z"/></svg>
      (555).240.3918
    </li>
    <li class="contact__item contact__item--gap">
      <svg class="icon" viewBox="0 0 14 14"><path d="M7 0a7 7 0 1 0 0 14A7 7 0 0 0 7 0zm0 1.3c.8.8 1.5 2.3 1.7 4.9H5.3C5.5 3.6 6.2 2.1 7 1.3zM1.3 7.8h2.6c.1 1.8.5 3.3 1.1 4.4A5.7 5.7 0 0 1 1.3 7.8zm0-1.6A5.7 5.7 0 0 1 5 1.8C4.4 2.9 4 4.4 3.9 6.2zm4 1.6h3.4C8.5 10.4 7.8 11.9 7 12.7c-.8-.8-1.5-2.3-1.7-4.9zm4.8 0h2.6A5.7 5.7 0 0 1 9 12.2c.6-1.1 1-2.6 1.1-4.4zm0-1.6C10 4.4 9.6 2.9 9 1.8a5.7 5.7 0 0 1 3.7 4.4z"/></svg>
      hartwellestates-demo.com
    </li>
    <li class="contact__item">
      <svg class="icon" viewBox="0 0 14 14"><path d="M0 3h14v1L7 8.2 0 4zm0 2.4 7 4.2 7-4.2V11H0z"/></svg>
      pembrook@hartwellestates-demo.com
    </li>
    <li class="contact__item contact__item--gap">
      <svg class="icon" viewBox="0 0 14 14"><path d="M7 0a4.8 4.8 0 0 0-4.8 4.8C2.2 8.4 7 14 7 14s4.8-5.6 4.8-9.2A4.8 4.8 0 0 0 7 0zm0 6.6a1.8 1.8 0 1 1 0-3.6 1.8 1.8 0 0 1 0 3.6z"/></svg>
      <span>418B W. Calloway Ave.<br>Larkmoor, KS. 70913</span>
    </li>
  </ul>
</section>

<section class="card card--back">
  <div class="emboss">
    <span class="emboss__dot"></span>
    <span class="emboss__name">Hartwell Estates</span>
  </div>
</section>

</body>
</html>
```